Card design for orthopaedic surgeons working as The Brightwater Joint Centre

Business cards, letterhead

Colors

Designer to choose colors to be used in the design.

Requirements
Must have
• Late addition.
• Cards letterhead must have logos of
• Crestmoor Lindell College of Surgeons
• Varenwood Bone Health Association
Nice to have
• Back of card to have space for appointment time to be added by hand and some blank space for writing incidental other notes.

```html
<!DOCTYPE html>
<html lang="en">
<head>
<meta charset="utf-8">
<title>The Brightwater Joint Centre — Business Card</title>
<link href="https://fonts.googleapis.com/css2?family=Ubuntu:wght@300;400&display=swap" rel="stylesheet">
<style>
  :root {
    --page-bg: #e8e5e1;
    --panel-dark: #1c2a36;
    --panel-mid: #2b3d4c;
    --face-light: #eef1f3;
    --face-shade: #d9dee2;
    --accent-blue: #2f8fe0;
    --accent-deep: #1a5fae;
    --text-light: #e4e9ee;
    --brand-navy: #1d3a52;
  }
  * { margin: 0; padding: 0; box-sizing: border-box; }
  html, body { width: 1200px; height: 969px; overflow: hidden; }
  body {
    background: var(--page-bg);
    font-family: "Ubuntu", sans-serif;
    position: relative;
  }
  .business-card {
    position: absolute;
    left: 141px; top: 223px;
    width: 918px; height: 523px;
    border-radius: 22px;
    overflow: hidden;
    background: linear-gradient(160deg, var(--face-light) 0%, var(--face-shade) 100%);
    box-shadow: 0 12px 30px rgba(0,0,0,0.18);
  }
  .card-shapes { position: absolute; inset: 0; }
  .contact-block {
    position: absolute;
    left: 53px; top: 114px;
    color: var(--text-light);
  }
  .person-name {
    font-size: 28px; font-weight: 400;
    letter-spacing: 1px;
    color: var(--accent-blue);
    line-height: 1.1;
  }
  .person-role {
    font-size: 18px; font-weight: 300;
    margin-top: 4px;
  }
  .address {
    font-size: 19px; font-weight: 300;
    line-height: 26px;
    margin-top: 22px;
  }
  .contact-list {
    list-style: none;
    margin-top: 20px;
  }
  .contact-list li {
    display: flex; align-items: center;
    height: 26px;
    font-size: 19px; font-weight: 300;
  }
  .contact-list li.small { font-size: 18px; }
  .contact-list svg {
    width: 16px; height: 16px;
    margin-right: 15px; flex: none;
    fill: var(--accent-blue);
  }
  .brand-name {
    position: absolute;
    left: 470px; top: 257px;
    width: 400px;
    text-align: center;
    font-size: 25px; font-weight: 400;
    color: var(--brand-navy);
    white-space: nowrap;
  }
</style>
</head>
<body>
  <div class="business-card">
    <svg class="card-shapes" viewBox="0 0 918 523" width="918" height="523">
      <defs>
        <linearGradient id="panelFill" x1="0" y1="0" x2="1" y2="1">
          <stop offset="0" stop-color="var(--panel-mid)"/>
          <stop offset="1" stop-color="var(--panel-dark)"/>
        </linearGradient>
      </defs>
      <path d="M0 0 H440 C395 45 375 110 395 200 C420 300 470 390 390 523 H0 Z" fill="url(#panelFill)"/>
      <path d="M440 0 C395 45 375 110 395 200 C420 300 470 390 390 523" fill="none" stroke="var(--accent-blue)" stroke-width="5"/>
      <path d="M400 300 C430 370 440 440 402 523" fill="none" stroke="var(--accent-deep)" stroke-width="3"/>
    </svg>

    <div class="contact-block">
      <h1 class="person-name">DANIEL HARROW</h1>
      <p class="person-role">President</p>
      <p class="address">4120 Elmstead Row<br>Fairbrook, Oregon 97512</p>
      <ul class="contact-list">
        <li><svg viewBox="0 0 16 16"><path d="M3 1l3 3-2 2c1 2 3 4 5 5l2-2 3 3-2 3C7 15 1 9 1 3z"/></svg>555-214-0387</li>
        <li><svg viewBox="0 0 16 16"><path d="M4 0h8v16H4zM5.5 2v10h5V2z"/></svg>555-618-2940</li>
        <li><svg viewBox="0 0 16 16"><path d="M4 1h8v4H4zM1 6h14v7H1zM4 10h8v5H4z"/></svg>555-730-4461</li>
        <li class="small"><svg viewBox="0 0 16 16"><path d="M1 3h14v10H1zM2 4l6 5 6-5v1l-6 5-6-5z"/></svg>daniel@brightwaterjoint.com</li>
        <li class="small"><svg viewBox="0 0 16 16"><path d="M8 1a7 7 0 100 14A7 7 0 008 1zM5 4c2 0 2 2 4 2s0 3-2 3-1 3-3 2S2 5 5 4zm6 4c2 0 2 3 0 4s-2-4 0-4z"/></svg>www.brightwaterjoint.com</li>
      </ul>
    </div>

    <p class="brand-name">The Brightwater Joint Centre</p>
  </div>
</body>
</html>
```